Website Design Project for Beauty & Wellness Professionals

As background information, I have a website that is focused on Beauty & Wellness Professionals:
- Job Search (www.lumarinovo.com)
- Business Classifieds (negocios.lumarinovo.com)
- Freelancer Classifieds (freelancer.lumarinovo.com)
- Course Reviews (cursos.lumarinovo.com)

All those websites use standard templates.

I need a DESIGN for the HOME PAGE (no coding) of the Website Platform that consolidates the four platforms under the same design.

Website designs that we like:
- quelvox.com
- brintmoor.com

Target Market(s)

Brazilian Professionals from Beauty & Wellness sector

Industry/Entity Type

Business

Requirements
Must have
• Website designs that we like:
- quelvox.com
- brintmoor.com

```html
<!DOCTYPE html>
<html lang="en">
<head>
<meta charset="utf-8">
<title>Lumarinovo Beauty — Home</title>
<link href="https://fonts.googleapis.com/css2?family=Source+Sans+3:wght@300;400;600&family=Fira+Sans+Condensed:wght@600&family=Arimo:ital,wght@0,400;0,700;1,700&display=swap" rel="stylesheet">
<style>
:root{
  --blue:#2d94c2;
  --blue-dark:#1f7fab;
  --link:#1c7fb6;
  --orange:#e0662f;
  --teal:#3aa39b;
  --ink:#333;
  --muted:#555;
  --page:#f4f4f4;
  --card-border:#d6d6d6;
  --footer:#333333;
  --footer-bar:#1e1e1e;
  --footer-text:#e6e6e6;
  --sans:"Source Sans 3",sans-serif;
  --body:"Arimo",Arial,sans-serif;
}
*{box-sizing:border-box;margin:0;padding:0}
html,body{width:823px;height:1200px;overflow:hidden}
body{position:relative;background:#fff;font-family:var(--body);color:var(--ink)}
.abs{position:absolute}

/* header */
.site-header{left:0;top:0;width:823px;height:89px;background:linear-gradient(#fff,#eeeeee)}
.brand{left:70px;top:30px;display:flex;align-items:center;gap:7px;font-family:var(--sans);font-weight:400;font-size:21px;color:var(--teal)}
.brand-dot{width:14px;height:14px;border-radius:50%;background:var(--teal)}
.social-label{left:296px;top:41px;font-family:var(--sans);font-size:12.5px;color:#444}
.social{top:34px;width:29px;height:29px;border-radius:50%}
.contact-phone{left:604px;top:30px;font-family:var(--sans);font-weight:600;font-size:17px;color:#222}
.contact-mail{left:609px;top:51px;font-family:var(--sans);font-size:12.5px;color:var(--link);text-decoration:underline}
.phone-icon{left:569px;top:34px}

/* nav */
.main-nav{left:0;top:89px;width:823px;height:32px;background:linear-gradient(var(--blue),var(--blue-dark));display:flex;align-items:center;padding-left:68px}
.main-nav a{font-family:var(--sans);font-size:12.5px;color:#fff;text-decoration:none;padding:0 19px;border-right:1px solid rgba(255,255,255,.35);line-height:18px}
.main-nav a:last-child{border-right:0}

/* hero */
.hero{left:0;top:121px;width:823px;height:236px;background:linear-gradient(180deg,#8a7a55 0%,#b99a66 35%,#6b4a2a 65%,#3d2c1a 100%)}
.hero-title{left:0;top:203px;width:823px;text-align:center;font-family:"Fira Sans Condensed",sans-serif;font-weight:600;font-size:32px;color:#fff;text-shadow:2px 2px 3px rgba(0,0,0,.6)}
.search-bar{left:93px;top:257px;width:614px;height:36px;background:rgba(30,22,14,.85);border-radius:3px}
.search-input{left:97px;top:260px;width:318px;height:30px;background:#fff;border-radius:3px;font-family:var(--sans);font-size:12.5px;color:#888;padding:8px 7px}
.search-select{left:426px;top:260px;width:193px;height:30px;background:#fff;border-radius:3px;font-family:var(--sans);font-size:12.5px;color:#888;padding:8px 10px}
.search-select .caret{position:absolute;right:0;top:5px;width:32px;height:20px;border-left:1px solid #ccc}
.search-btn{left:624px;top:260px;width:78px;height:30px;background:var(--orange);border-radius:3px;font-family:var(--sans);font-size:17px;color:#fff;text-align:center;line-height:30px}

/* about */
.band{left:0;top:357px;width:823px;height:423px;background:var(--page)}
.section-title{font-family:var(--sans);font-weight:300;color:#222}
.what-title{left:78px;top:378px;font-size:25px}
.what-rule{left:78px;top:410px;width:450px;border-top:1px dotted #bbb}
.what-text{left:80px;top:418px;width:452px;font-size:8.4px;line-height:15.2px;color:#333}
.what-text p+p{margin-top:15px}
.more-btn{left:79px;top:533px;width:56px;height:17px;background:var(--orange);border-radius:9px;font-size:8.5px;color:#fff;padding:3px 0 0 10px}
.more-btn .plus{position:absolute;right:-2px;top:-1px;width:19px;height:19px;border-radius:50%;background:#f1f1f1;border:1px solid #ccc;font-size:13px;color:#666;text-align:center;line-height:16px}
.promo{left:546px;top:381px;width:207px;height:172px;border:1px solid #cfcfcf;background:#fff}
.promo-photo{position:absolute;left:0;top:0;width:105px;height:170px;background:linear-gradient(135deg,#f3ddcc,#e4bfa6 60%,#f7ece3)}
.promo-brand{position:absolute;right:8px;top:66px;font-family:var(--sans);font-size:18px;color:var(--teal)}
.promo-text{position:absolute;right:8px;top:97px;width:100px;text-align:right;font-family:var(--sans);font-size:10.3px;line-height:12.4px;color:#444}
.divider{left:72px;top:567px;width:681px;border-top:1px dotted #bbb}

/* tabs */
.tab{top:590px;height:30px;font-family:var(--sans);font-weight:300;font-size:17.5px;color:#222;padding-top:4px}
.tab.active{left:78px;width:111px;background:#fff;border:1px solid #ddd;border-bottom:0;color:var(--link);text-align:center;border-radius:3px 3px 0 0}
.reviews{left:78px;top:620px;width:454px;height:150px;background:#fff;border:1px solid #ddd}
.review{position:absolute;left:0;width:452px;height:74px}
.review + .review{border-top:1px solid #eee}
.review-logo{position:absolute;left:13px;top:10px;width:52px;height:52px;border-radius:2px}
.review-name{position:absolute;left:76px;top:9px;font-weight:700;font-size:10px;color:var(--link)}
.stars{position:absolute;left:76px;top:24px}
.review-count{position:absolute;left:76px;top:42px;font-size:7.6px;color:#666}
.review-quote{position:absolute;left:152px;top:8px;width:290px;font-weight:700;font-size:8.8px;line-height:12.4px;color:var(--link)}
.review-body{position:absolute;left:154px;top:35px;width:270px;font-size:8px;line-height:11px;color:#444}
.read-more{position:absolute;right:18px;top:59px;font-style:italic;font-size:7.6px;line-height:10px;color:#333}
.ad{left:547px;top:602px;width:206px;height:163px;background:linear-gradient(160deg,#bdbdbd,#9d9d9d 55%,#d8d8d8)}

/* professionals */
.pro-title{left:75px;top:797px;font-size:22px}
.card{top:834px;width:158px;height:157px;background:#fff;border:1px solid var(--card-border);border-radius:3px;box-shadow:0 0 0 2px #f2f2f2}
.card.active{background:#eef3f7}
.card-photo{position:absolute;left:5px;top:5px;width:146px;height:83px}
.card-title{position:absolute;left:6px;top:95px;font-weight:700;font-size:10px;letter-spacing:.2px;color:var(--link)}
.card-text{position:absolute;left:6px;top:110px;width:148px;font-size:8px;line-height:11px;color:#333}

/* footer */
.site-footer{left:0;top:1025px;width:823px;height:154px;background:var(--footer)}
.foot-head{top:1044px;font-family:var(--sans);font-weight:300;font-size:15.5px;color:var(--footer-text);padding-bottom:11px;border-bottom:1px solid #444}
.foot-list{left:80px;top:1090px;list-style:none;font-size:8px;color:#fff}
.foot-list li{line-height:16px;padding-left:9px;position:relative}
.foot-list li::before{content:"";position:absolute;left:0;top:6px;width:3px;height:3px;border-radius:50%;background:var(--blue)}
.tweet-avatar{left:197px;top:1098px;width:21px;height:21px;background:linear-gradient(#e3b04a,#6a8fb0);border-radius:2px}
.tweet-name{left:222px;top:1098px;font-size:8px;font-weight:700;color:#fff}
.tweet-handle{left:222px;top:1109px;font-size:8px;color:#aaa}
.tweet-date{left:389px;top:1099px;font-size:7px;color:#aaa}
.tweet-text{left:197px;top:1123px;width:215px;font-size:8px;line-height:11px;color:#ddd}
.news-text{left:446px;top:1088px;width:160px;font-size:8px;line-height:13.5px;color:#eee}
.news-input{left:446px;top:1141px;width:158px;height:23px;background:#e9e9e9;font-size:8px;color:#999;padding:7px 0 0 23px}
.about-text{left:628px;top:1089px;width:130px;font-size:8px;line-height:13.5px;color:#eee}
.foot-brand{left:618px;top:1152px;width:140px;text-align:center;white-space:nowrap;font-family:var(--sans);font-size:14px;line-height:18px;color:#ccc}
.footer-bar{left:0;top:1179px;width:823px;height:21px;background:var(--footer-bar);text-align:center;font-size:8.3px;color:#eee;line-height:21px}
</style>
</head>
<body>

<header class="site-header abs"></header>
<div class="brand abs"><span class="brand-dot"></span>Lumarinovo Beauty</div>
<div class="social-label abs">Connected Stay:</div>
<span class="social abs" style="left:387px;background:#1d4f82" aria-label="Social profile 1"></span>
<span class="social abs" style="left:422px;background:#27a1dd" aria-label="Social profile 2"></span>
<span class="social abs" style="left:458px;background:#f28e13" aria-label="Feed"></span>
<span class="social abs" style="left:493px;background:#9b9b9b" aria-label="Email"></span>
<svg class="phone-icon abs" width="28" height="28" viewBox="0 0 28 28" aria-hidden="true">
  <circle cx="14" cy="14" r="13" fill="#e2e2e2" stroke="#c9c9c9"/>
  <path d="M9 7c1-1 2-1 3 0l1 3c0 1-1 2-1 2 1 2 2 3 4 4 0 0 1-1 2-1l3 1c1 1 1 2 0 3-2 2-5 1-8-2s-5-7-4-10z" fill="#555"/>
</svg>
<div class="contact-phone abs">(312)-555-(0148)</div>
<div class="contact-mail abs">info@lumarinovo.com</div>

<nav class="main-nav abs">
  <a>Home</a><a>Categories of Business</a><a>For Professionals</a><a>For Business</a><a>About Us</a><a>Contact Us</a>
</nav>

<div class="hero abs" role="img" aria-label="Photo of a fishing boat moored on a calm lake at the foot of wooded hills"></div>
<h1 class="hero-title abs">Welcome to the presentation of Lumarinovo Beauty</h1>
<div class="search-bar abs"></div>
<div class="search-input abs">what are you looking for?</div>
<div class="search-select abs">All Categories
  <span class="caret"><svg width="32" height="20" viewBox="0 0 32 20"><path d="M10 8h12l-6 6z" fill="#333"/></svg></span>
</div>
<div class="search-btn abs">Search</div>

<section class="band abs"></section>
<h2 class="section-title what-title abs">What We Do</h2>
<div class="what-rule abs"></div>
<div class="what-text abs">
  <p><b><i>Lorem Ipsum is simply dummy text of the printing and typesetting industry. Lorem Ipsum has been the industry's standard dummy text ever since the 1500s,</i></b> when an unknown printer took a galley of type and scrambled it to make a type specimen book. It has survived not only five centuries, but also the leap into electronic typesetting, remaining essentially unchanged.</p>
  <p>It was popularised in the 1960s with the release of Typeline sheets containing Lorem Ipsum passages, and more recently with desktop publishing software like Quillset Composer including versions of Lorem Ipsum.</p>
</div>
<div class="more-btn abs">More<span class="plus">+</span></div>
<div class="promo abs">
  <div class="promo-photo" role="img" aria-label="Photo of a woman holding a white orchid"></div>
  <div class="promo-brand">Lumarinovo Beauty</div>
  <div class="promo-text">when an unknown printer took a galley of type and scrambled it to make a type specimen book.</div>
</div>
<div class="divider abs"></div>

<div class="tab active abs">Recents</div>
<div class="tab abs" style="left:203px">Most Viewed</div>
<div class="tab abs" style="left:331px">Random</div>
<div class="reviews abs">
  <div class="review" style="top:0">
    <div class="review-logo" style="background:#111" role="img" aria-label="Telvana badge"></div>
    <div class="review-name">Telvana</div>
    <svg class="stars" width="62" height="12" viewBox="0 0 62 12"><g id="st"><path d="M6 0l1.8 3.9 4.2.4-3.2 2.8 1 4.1L6 9 2.2 11.2l1-4.1L0 4.3l4.2-.4z" fill="#3c9a3c"/></g><use href="#st" x="12.5"/><use href="#st" x="25"/><path d="M43.5 0l1.8 3.9 4.2.4-3.2 2.8 1 4.1-3.8-2.2-3.8 2.2 1-4.1-3.2-2.8 4.2-.4z" fill="#ccc"/><path d="M56 0l1.8 3.9 4.2.4-3.2 2.8 1 4.1L56 9l-3.8 2.2 1-4.1-3.2-2.8 4.2-.4z" fill="#ccc"/></svg>
    <div class="review-count">1,429 reviews</div>
    <div class="review-quote">“ simply dummy text of the printing and typesetting industry. Lorem Ipsum has been the industry's</div>
    <div class="review-body">simply dummy text of the printing and typesetting industry. Lorem Ipsum has been the industry's</div>
    <div class="read-more">read more...</div>
  </div>
  <div class="review" style="top:74px">
    <div class="review-logo" style="background:#b8242e" role="img" aria-label="Norbank badge"></div>
    <div class="review-name">Norbank</div>
    <svg class="stars" width="62" height="12" viewBox="0 0 62 12"><use href="#st"/><use href="#st" x="12.5"/><use href="#st" x="25"/><path d="M43.5 0l1.8 3.9 4.2.4-3.2 2.8 1 4.1-3.8-2.2-3.8 2.2 1-4.1-3.2-2.8 4.2-.4z" fill="#ccc"/><path d="M56 0l1.8 3.9 4.2.4-3.2 2.8 1 4.1L56 9l-3.8 2.2 1-4.1-3.2-2.8 4.2-.4z" fill="#ccc"/></svg>
    <div class="review-count">820 reviews</div>
    <div class="review-quote">“ simply dummy text of the printing and typesetting industry. Lorem Ipsum has been the industry's „</div>
    <div class="review-body">simply dummy text of the printing and typesetting industry. Lorem Ipsum has been the industry's</div>
    <div class="read-more">read more...</div>
  </div>
</div>
<div class="ad abs" role="img" aria-label="Advertisement for pricing tables shown on a laptop and a phone"></div>

<h2 class="section-title pro-title abs">Beauty &amp; Wellness Professionals</h2>
<div class="card active abs" style="left:73px">
  <div class="card-photo" role="img" aria-label="Photo of a woman working on a laptop" style="background:linear-gradient(135deg,#e9e2d6,#bfae94 60%,#7c6a58)"></div>
  <div class="card-title">Job Search</div>
  <div class="card-text">simply dummy text of the printing and typesetting industry. Lorem Ipsum has been the industry's</div>
</div>
<div class="card abs" style="left:247px">
  <div class="card-photo" role="img" aria-label="Photo of business people in a meeting" style="background:linear-gradient(135deg,#6d7a88,#2b2f36 55%,#a9adb3)"></div>
  <div class="card-title">Business Classifieds</div>
  <div class="card-text">simply dummy text of the printing and typesetting industry. Lorem Ipsum has been the industry's</div>
</div>
<div class="card abs" style="left:421px">
  <div class="card-photo" role="img" aria-label="Photo of a makeup artist applying makeup" style="background:linear-gradient(135deg,#d8d5d1,#b58b73 55%,#2e2a28)"></div>
  <div class="card-title">Freelancer Classifieds</div>
  <div class="card-text">simply dummy text of the printing and typesetting industry. Lorem Ipsum has been the industry's</div>
</div>
<div class="card abs" style="left:595px">
  <div class="card-photo" role="img" aria-label="Photo of a facial spa treatment" style="background:linear-gradient(135deg,#e7c9c6,#f3ece9 55%,#d89b9a)"></div>
  <div class="card-title" style="top:98px">Course Reviews</div>
  <div class="card-text" style="top:113px">simply dummy text of the printing and typesetting industry. Lorem Ipsum has been the industry's</div>
</div>

<footer class="site-footer abs"></footer>
<div class="foot-head abs" style="left:80px;width:93px">Navigation</div>
<div class="foot-head abs" style="left:197px;width:226px">Latest tweets</div>
<div class="foot-head abs" style="left:446px;width:158px">Newsletter</div>
<div class="foot-head abs" style="left:628px;width:123px">About us</div>
<ul class="foot-list abs"><li>About Us</li><li>Best sellers</li><li>News</li><li>Collections</li></ul>
<div class="tweet-avatar abs" role="img" aria-label="Profile picture"></div>
<div class="tweet-name abs">Brightwell</div>
<div class="tweet-handle abs">@TheBrightwell</div>
<div class="tweet-date abs">11 Jul</div>
<div class="tweet-text abs">We are in the final stages of building our latest product - Solenne for SiteForge. It's going to use the amazing ShopForge plugin.</div>
<div class="news-text abs">Vestibulum at lacus id turpis malesuada varius. Donec ultricies mauris vel nisi porta dictum.</div>
<div class="news-input abs">
  <svg style="position:absolute;left:8px;top:7px" width="10" height="8" viewBox="0 0 10 8"><rect x=".5" y=".5" width="9" height="7" fill="none" stroke="#555"/><path d="M.5 .5l4.5 4 4.5-4" fill="none" stroke="#555"/></svg>
  e-mail address
</div>
<div class="about-text abs">Solenne is a modern responsive HTML5 theme</div>
<div class="foot-brand abs">Lumarinovo Beauty</div>
<div class="footer-bar abs">Except where noted, copyright © 2010-2012 Lumarinovo Beauty</div>

</body>
</html>
```